Oil and Gas Exploration and Production company needs a business card design

We need a business card design using our logo and colors in the logo. We want a mainstream design.

```html
<!DOCTYPE html>
<html lang="en">
<head>
<meta charset="utf-8">
<title>Solano Oil &amp; Gas – Business Card</title>
<link rel="stylesheet" href="https://fonts.googleapis.com/css2?family=Arimo:wght@400;700&display=swap">
<style>
  :root {
    --backdrop: #2b2b2b;
    --card: #ffffff;
    --ink: #111111;
    --gold: #b8862a;
    --charcoal: #1f1f1f;
  }
  * { margin: 0; padding: 0; box-sizing: border-box; }
  html, body {
    width: 1200px;
    height: 997px;
    overflow: hidden;
    background: var(--backdrop);
    font-family: "Arimo", Arial, sans-serif;
  }
  .business-card {
    position: absolute;
    left: 180px;
    top: 258px;
    width: 840px;
    height: 480px;
    background: var(--card);
    overflow: hidden;
    box-shadow: 0 18px 40px rgba(0,0,0,0.45);
  }
  .accent-disc {
    position: absolute;
    right: -90px;
    top: 40px;
    width: 440px;
    height: 440px;
    border-radius: 50%;
    background: var(--charcoal);
  }
  .brand {
    position: absolute;
    left: 56px;
    top: 62px;
    display: flex;
    align-items: center;
    gap: 14px;
  }
  .brand-dot {
    width: 34px;
    height: 34px;
    border-radius: 50%;
    background: var(--charcoal);
  }
  .brand-name {
    font-weight: 700;
    font-size: 44px;
    color: var(--ink);
    letter-spacing: 0.5px;
    line-height: 1;
  }
  .info-group {
    position: absolute;
    left: 56px;
    padding-left: 20px;
    border-left: 5px solid var(--ink);
  }
  .info-group.gold-rule { border-left-color: var(--gold); }
  .person { top: 200px; }
  .person-name {
    font-weight: 700;
    font-size: 26px;
    color: var(--gold);
    line-height: 1.1;
  }
  .person-title {
    font-size: 19px;
    color: var(--ink);
    margin-top: 2px;
  }
  .address {
    top: 282px;
    font-size: 17px;
    line-height: 1.35;
    color: var(--gold);
  }
  .contacts {
    top: 352px;
    list-style: none;
  }
  .contacts li {
    display: flex;
    align-items: center;
    gap: 12px;
    font-size: 19px;
    color: var(--ink);
    height: 32px;
  }
  .contacts li.web { color: var(--gold); font-weight: 700; }
  .contact-icon {
    width: 22px;
    height: 22px;
    flex: none;
  }
</style>
</head>
<body>
  <div class="business-card">
    <div class="accent-disc"></div>

    <div class="brand">
      <span class="brand-dot"></span>
      <span class="brand-name">Solano Oil &amp; Gas</span>
    </div>

    <div class="info-group person">
      <p class="person-name">Maren Holt</p>
      <p class="person-title">Director of Sales &amp; Marketing</p>
    </div>

    <div class="info-group gold-rule address">
      <p>Fenwick Road Bramhall</p>
      <p>Stockport SK7 2QL</p>
    </div>

    <ul class="info-group contacts">
      <li>
        <svg class="contact-icon" viewBox="0 0 22 22" aria-hidden="true">
          <circle cx="11" cy="11" r="11" fill="#b8862a"/>
          <path d="M7 6.5c.8-.8 1.6-.6 2 .2l.8 1.5c.3.6.1 1.1-.4 1.5l-.6.4c.6 1.3 1.6 2.3 2.9 2.9l.4-.6c.4-.5.9-.7 1.5-.4l1.5.8c.8.4 1 1.2.2 2-1 1-2.6 1.1-4.6-.3-1.6-1.1-2.9-2.4-4-4C5.3 9.1 6 7.5 7 6.5z" fill="#fff"/>
        </svg>
        <span>614 320 5287</span>
      </li>
      <li>
        <svg class="contact-icon" viewBox="0 0 22 22" aria-hidden="true">
          <circle cx="11" cy="11" r="11" fill="#b8862a"/>
          <rect x="7.5" y="5" width="7" height="12" rx="1.3" fill="none" stroke="#fff" stroke-width="1.5"/>
          <circle cx="11" cy="14.6" r="0.9" fill="#fff"/>
        </svg>
        <span>maren@solanoenergy.com</span>
      </li>
      <li class="web">
        <svg class="contact-icon" viewBox="0 0 22 22" aria-hidden="true">
          <circle cx="11" cy="11" r="11" fill="#b8862a"/>
          <rect x="5.5" y="7" width="11" height="8" rx="1" fill="none" stroke="#fff" stroke-width="1.4"/>
          <path d="M5.8 7.5 11 11.5l5.2-4" fill="none" stroke="#fff" stroke-width="1.4"/>
        </svg>
        <span>www.solano-energy.co.uk</span>
      </li>
    </ul>
  </div>
</body>
</html>
```